I need new business cards designed

I would like to get some new designs on business cards. I will upload my logo for reference. The business cards that were designed for me a few months ago were too difficult for the print companies to work with. My company is Quillbrook.net LLC. It is an art company that sells painting and expression cards online.

```html
<!DOCTYPE html>
<html lang="en">
<head>
<meta charset="utf-8">
<title>Quillbrook.net LLC – Business Cards</title>
<link rel="stylesheet" href="https://fonts.googleapis.com/css2?family=Open+Sans:wght@400;600;700&display=swap">
<style>
  :root {
    --bg-light: #e4e3e0;
    --bg-dark: #b9b8b4;
    --card: #ffffff;
    --blue: #0ea0dc;
    --green: #8dc63f;
    --navy: #353a7c;
    --ink: #2b2b2b;
    --font: "Open Sans", Arial, sans-serif;
  }
  * { box-sizing: border-box; margin: 0; padding: 0; }
  html, body { width: 1200px; height: 801px; overflow: hidden; }
  body {
    background: linear-gradient(160deg, var(--bg-light), var(--bg-dark));
    font-family: var(--font);
    position: relative;
  }
  .card {
    position: absolute;
    top: 236px;
    width: 560px;
    height: 320px;
    background: var(--card);
    border-radius: 18px;
    box-shadow: 0 4px 0 var(--blue), 0 14px 28px rgba(0,0,0,.22);
    overflow: hidden;
  }
  .card--front { left: 25px; }
  .card--back { left: 615px; }

  .front-band { position: absolute; inset: 0; width: 100%; height: 100%; }

  .brand { display: flex; align-items: center; gap: 10px; }
  .brand__square { background: var(--navy); flex: none; }
  .brand__name { color: var(--navy); font-weight: 400; line-height: 1; white-space: nowrap; }
  .brand__tagline { color: var(--blue); font-weight: 400; line-height: 1.2; white-space: nowrap; }

  .card--front .brand { position: absolute; left: 34px; top: 206px; }
  .card--front .brand__square { width: 52px; height: 52px; }
  .card--front .brand__name { font-size: 27px; }
  .card--front .brand__tagline { font-size: 11.5px; margin-top: 3px; }

  .divider {
    position: absolute; left: 300px; top: 172px;
    width: 1.5px; height: 124px; background: var(--blue);
  }
  .contact { position: absolute; left: 318px; top: 108px; color: var(--ink); }
  .contact__name { color: var(--blue); font-weight: 700; font-size: 19px; letter-spacing: .5px; }
  .contact__title { font-size: 12px; margin-bottom: 8px; }
  .contact__line { font-size: 12px; line-height: 1.55; display: flex; align-items: center; gap: 6px; }
  .contact__icon { width: 11px; height: 11px; flex: none; }
  .contact__spacer { height: 8px; }

  .social { position: absolute; right: 26px; bottom: 34px; display: flex; gap: 7px; }
  .social span { width: 13px; height: 13px; border-radius: 50%; background: var(--blue); }

  .card--back .brand { position: absolute; left: 42px; top: 112px; gap: 18px; }
  .card--back .brand__square { width: 92px; height: 92px; }
  .card--back .brand__name { font-size: 48px; }
  .card--back .brand__tagline { font-size: 21px; margin-top: 6px; }
</style>
</head>
<body>
  <section class="card card--front">
    <svg class="front-band" viewBox="0 0 560 320" preserveAspectRatio="none" aria-hidden="true">
      <path d="M0,0 H560 V62 C420,70 260,95 120,150 C70,170 30,185 0,198 Z" fill="var(--green)"/>
      <path d="M0,212 C40,194 90,176 130,162 C270,108 420,82 560,70" fill="none" stroke="var(--blue)" stroke-width="7"/>
    </svg>

    <div class="brand">
      <span class="brand__square"></span>
      <div>
        <div class="brand__name">Quillbrook.net</div>
        <div class="brand__tagline">Paint Freely · Boldly · Kindly</div>
      </div>
    </div>

    <div class="divider"></div>

    <div class="contact">
      <div class="contact__name">NORA LINDQVIST</div>
      <div class="contact__title">Managing Director</div>
      <div class="contact__line">Your address, City</div>
      <div class="contact__line">State, Zip 1234</div>
      <div class="contact__spacer"></div>
      <div class="contact__line">
        <svg class="contact__icon" viewBox="0 0 12 12" aria-hidden="true"><path d="M2.5 1 L4.5 1 L5.2 3.6 L4 4.6 C4.6 6 5.8 7.3 7.3 8 L8.3 6.8 L11 7.5 L11 9.5 C11 10.3 10.3 11 9.5 11 C5 10.7 1.3 7 1 2.5 C1 1.7 1.7 1 2.5 1 Z" fill="var(--blue)"/></svg>
        555-014-2368
      </div>
      <div class="contact__line">
        <svg class="contact__icon" viewBox="0 0 12 12" aria-hidden="true"><rect x="0.5" y="2" width="11" height="8" rx="1" fill="var(--blue)"/><path d="M1 2.8 L6 6.6 L11 2.8" fill="none" stroke="#fff" stroke-width="1"/></svg>
        hello@quillbrook.net
      </div>
      <div class="contact__line">
        <svg class="contact__icon" viewBox="0 0 12 12" aria-hidden="true"><circle cx="6" cy="6" r="5.2" fill="var(--blue)"/><path d="M0.8 6 H11.2 M6 0.8 C3.5 3.5 3.5 8.5 6 11.2 M6 0.8 C8.5 3.5 8.5 8.5 6 11.2" fill="none" stroke="#fff" stroke-width=".8"/></svg>
        www.Quillbrook.net
      </div>
    </div>

    <div class="social" aria-label="Social profiles">
      <span></span><span></span><span></span>
    </div>
  </section>

  <section class="card card--back">
    <div class="brand">
      <span class="brand__square"></span>
      <div>
        <div class="brand__name">Quillbrook.net</div>
        <div class="brand__tagline">Paint Freely · Boldly · Kindly</div>
      </div>
    </div>
  </section>
</body>
</html>
```